Round Label Sticker 2.5-3 inch diameter

We need a design for a sticker to distribute for more brand recognition and product outreach.
My company The Brisk Lark Company Ltd. Specializes in working with people with diabetes. My products are made for diabetics because they have no added sugars, high in protein and fiber and each serving is lower than 5% daily value of carbohydrates.
I am a dietitian and my dad passed away from diabetes. I have created a growing food and beverage line that will give more joy into a diabetic's life while providing more food options that make them feel happy instead of guilty when they eat it.
I am teaching cooking classes to promote my products as well as doing exhibits and events. I want to give away a sticker to people that reads "I'm too sweet for sugar!" and somewhere on it would be my logo as well as my website info. www.brisklark-example.com
The sticker should make people smile and warm as well as draw interest to my product line.
Target Market(s)
Diabetes and people who do not want added sugars in their food
Industry/Entity Type
Food Store
Requirements
Must have
- my logo and website

```html
<!DOCTYPE html>
<html lang="en">
<head>
<meta charset="utf-8">
<title>Brisk Lark – I'm too sweet for sugar sticker</title>
<link rel="stylesheet" href="https://fonts.googleapis.com/css2?family=Bebas+Neue&family=Kaushan+Script&family=Josefin+Sans:wght@600&display=swap">
<style>
  :root {
    --page: #ffffff;
    --plum-deep: #35264f;
    --plum: #4b3669;
    --plum-soft: #6a5388;
    --citrus: #b86a68;
    --citrus-glow: #cf8a79;
    --ink-light: #ffffff;
  }
  html, body {
    margin: 0;
    padding: 0;
    width: 1200px;
    height: 1157px;
    overflow: hidden;
    background: var(--page);
  }
  .sticker {
    display: block;
    width: 1200px;
    height: 1157px;
  }
  .brand-name {
    font-family: "Josefin Sans", sans-serif;
    font-weight: 600;
    font-size: 58px;
    letter-spacing: 6px;
    fill: var(--ink-light);
  }
  .script-line {
    font-family: "Kaushan Script", cursive;
    fill: var(--ink-light);
  }
  .display-line {
    font-family: "Bebas Neue", sans-serif;
    fill: var(--ink-light);
  }
  .web-address {
    font-family: "Josefin Sans", sans-serif;
    font-weight: 600;
    font-size: 54px;
    letter-spacing: 2px;
    fill: var(--ink-light);
  }
</style>
</head>
<body>
<svg class="sticker" viewBox="0 0 1200 1157" xmlns="http://www.w3.org/2000/svg">
  <defs>
    <radialGradient id="orchardTones" cx="0.43" cy="0.5" r="0.6">
      <stop offset="0" stop-color="var(--citrus-glow)"/>
      <stop offset="0.22" stop-color="var(--citrus)"/>
      <stop offset="0.5" stop-color="var(--plum-soft)"/>
      <stop offset="0.8" stop-color="var(--plum)"/>
      <stop offset="1" stop-color="var(--plum-deep)"/>
    </radialGradient>
    <path id="addressArc" d="M 160 578 A 440 440 0 0 0 1040 578"/>
  </defs>

  <circle class="sticker-photo" cx="600" cy="578" r="543" fill="url(#orchardTones)"
          role="img" aria-label="Photo of ripe oranges hanging among leaves on a tree, tinted purple"/>

  <g class="brand-mark">
    <text class="brand-name" x="600" y="160" text-anchor="middle">BRISK LARK</text>
  </g>

  <g class="slogan">
    <text class="script-line" x="600" y="378" font-size="150" text-anchor="middle">I'm too</text>
    <text class="display-line" x="250" y="636" font-size="228" textLength="392" lengthAdjust="spacingAndGlyphs">SWEET</text>
    <text class="script-line" x="710" y="628" font-size="150">for</text>
    <text class="display-line" x="600" y="886" font-size="228" text-anchor="middle">SUGAR!</text>
  </g>

  <text class="web-address">
    <textPath href="#addressArc" startOffset="50%" text-anchor="middle">www.brisklark-example.com</textPath>
  </text>
</svg>
</body>
</html>
```